Business Card Design for company

We want new business cards. We'd like something different-- yet still highly professional. Our tagline is Providing leadership, delivering success. Stock photos are ok, as long as they are relevant and look upscale.

Target Market(s)

Architecture/Business Management Consulting/Engineering Consulting

Contact Information for Business Card

dark gray background with pops of blue might be good, but you tell me. You're the designers. Rounded corners might be nice, but again, you tell me.

Font styles to use
Serif
Sans Serif

Colors
3276b5
5c5c5c
9d9d9d
fbfbfb

Requirements
Nice to have
• Something different, but still very professional.

```html
<!DOCTYPE html>
<html lang="en">
<head>
<meta charset="utf-8">
<title>Norvale Partners – Business Card</title>
<link href="https://fonts.googleapis.com/css2?family=Roboto:wght@400;500;700&display=swap" rel="stylesheet">
<style>
  :root {
    --backdrop: #2a2a2b;
    --card-white: #ffffff;
    --card-grey: #4a4d52;
    --brand-blue: #2d6399;
    --text-dark: #444648;
    --text-mid: #5c5c5c;
    --rule: #6a6a6a;
    --white: #fbfbfb;
  }
  html, body {
    margin: 0;
    padding: 0;
    width: 1125px;
    height: 1200px;
    overflow: hidden;
    background: var(--backdrop);
    font-family: "Roboto", Arial, sans-serif;
  }
  .canvas {
    position: relative;
    width: 1125px;
    height: 1200px;
  }
  .card {
    position: absolute;
    left: 150px;
    width: 825px;
  }
  .card-front {
    top: 98px;
    height: 472px;
    background: var(--card-white);
  }
  .card-back {
    top: 631px;
    height: 470px;
    background: var(--card-grey);
  }
  .brand-mark {
    position: absolute;
    right: 47px;
    top: 150px;
    text-align: right;
    color: var(--brand-blue);
    font-weight: 700;
    line-height: 1;
  }
  .brand-mark .brand-main {
    display: block;
    font-size: 88px;
    letter-spacing: -1px;
  }
  .brand-mark .brand-sub {
    display: block;
    font-size: 28px;
    letter-spacing: 2px;
    margin-top: 14px;
  }
  .holder-name {
    position: absolute;
    left: 43px;
    top: 250px;
    margin: 0;
    font-size: 29px;
    font-weight: 700;
    color: var(--brand-blue);
  }
  .holder-title {
    position: absolute;
    left: 44px;
    top: 284px;
    margin: 0;
    font-size: 20px;
    font-weight: 500;
    color: var(--text-dark);
  }
  .divider {
    position: absolute;
    left: 43px;
    right: 45px;
    top: 316px;
    height: 2px;
    background: var(--rule);
  }
  .contact-list {
    position: absolute;
    left: 44px;
    top: 329px;
    margin: 0;
    padding: 0;
    list-style: none;
  }
  .contact-list li {
    display: flex;
    align-items: center;
    height: 26.5px;
    font-size: 19.5px;
    color: var(--text-dark);
  }
  .contact-list svg {
    width: 18px;
    height: 18px;
    margin-right: 12px;
    fill: var(--brand-blue);
  }
  .address {
    position: absolute;
    right: 45px;
    top: 360px;
    margin: 0;
    text-align: right;
    font-style: normal;
    font-size: 19.5px;
    line-height: 25.5px;
    color: var(--text-mid);
  }
  .edge-rule {
    position: absolute;
    left: 0;
    right: 0;
    top: 455px;
    height: 2px;
    background: var(--text-dark);
  }
  .edge-band {
    position: absolute;
    left: 0;
    right: 0;
    bottom: 0;
    height: 13px;
    background: var(--brand-blue);
  }
  .back-name {
    position: absolute;
    left: 0;
    right: 0;
    top: 150px;
    margin: 0;
    text-align: center;
    font-size: 140px;
    font-weight: 500;
    color: var(--white);
    line-height: 1;
  }
  .tagline {
    position: absolute;
    left: 0;
    right: 0;
    top: 393px;
    margin: 0;
    text-align: center;
    font-size: 20.5px;
    color: var(--white);
  }
  .tagline .dot {
    margin: 0 10px;
  }
</style>
</head>
<body>
<main class="canvas">
  <section class="card card-front" aria-label="Card front">
    <div class="brand-mark">
      <span class="brand-main">NORVALE</span>
      <span class="brand-sub">PARTNERS</span>
    </div>
    <h1 class="holder-name">DANIEL REYES</h1>
    <p class="holder-title">CEO/FOUNDER</p>
    <div class="divider"></div>
    <ul class="contact-list">
      <li>
        <svg viewBox="0 0 24 24" aria-hidden="true"><path d="M6.6 10.8a15.1 15.1 0 0 0 6.6 6.6l2.2-2.2a1 1 0 0 1 1-.25 11.4 11.4 0 0 0 3.6.57 1 1 0 0 1 1 1V20a1 1 0 0 1-1 1A17 17 0 0 1 3 4a1 1 0 0 1 1-1h3.5a1 1 0 0 1 1 1c0 1.25.2 2.45.57 3.57a1 1 0 0 1-.25 1z"/></svg>
        555 214 7730
      </li>
      <li>
        <svg viewBox="0 0 24 24" aria-hidden="true"><path d="M7 1h10a2 2 0 0 1 2 2v18a2 2 0 0 1-2 2H7a2 2 0 0 1-2-2V3a2 2 0 0 1 2-2zm0 3v14h10V4zm5 15.5a1 1 0 1 0 0 2 1 1 0 0 0 0-2z"/></svg>
        555 318 4926
      </li>
      <li>
        <svg viewBox="0 0 24 24" aria-hidden="true"><path d="M6 2h9l3 3v4H6zM3 10h18a2 2 0 0 1 2 2v8H1v-8a2 2 0 0 1 2-2zm3 4v2h12v-2z"/></svg>
        555 407 1582
      </li>
      <li>
        <svg viewBox="0 0 24 24" aria-hidden="true"><path d="M2 5h20v14H2zm2 2v.4l8 5.2 8-5.2V7zm0 2.8V17h16V9.8l-8 5.2z"/></svg>
        daniel@norvalepartners.com
      </li>
    </ul>
    <address class="address">
      1240 Harbor View Road<br>
      Juneau, Alaska 99801<br>
      www.norvalepartners.com
    </address>
    <div class="edge-rule"></div>
    <div class="edge-band"></div>
  </section>

  <section class="card card-back" aria-label="Card back">
    <p class="back-name">Norvale</p>
    <p class="tagline">Providing leadership<span class="dot">•</span>delivering success</p>
  </section>
</main>
</body>
</html>
```